Ferncrest Roam Wording For Logo & Business card

I have the logo, I just need the "Ferncrest Roam" wording to go with it, and a business card design. The only thing on the business card is the website info. We provide nature connection experiences, and bolster these efforts through writing and host a platform for community around it.

I also have an idea of what it could look like (sketch), though I'm really not sure how it would come out. I am open to the best design and happy to consider original artwork. You can see what the site is about at FerncrestRoam.example.

Contact Information for Business Card

The only thing on the business card is the website info and the design. I will put other messaging on the back.

Website lettering (FerncrestRoam.example) in Montserrat

Logo Text

Ferncrest Roam (letters optional)

Font styles to use
Other font styles liked:
• montserrat

```html
<!DOCTYPE html>
<html lang="en">
<head>
<meta charset="utf-8">
<title>Ferncrest Roam – Business Card</title>
<link rel="stylesheet" href="https://fonts.googleapis.com/css2?family=Montserrat:wght@500;600;700&display=swap">
<style>
  :root {
    --page: #e9e9e7;
    --card-white: #f7f7f6;
    --ink: #1b1430;
    --ink-soft: #2b2b2b;
    --accent-red: #d1280f;
    --plum: #2a1840;
    --flame-orange: #e4570a;
    --flame-deep: #c23d06;
    --flame-yellow: #f8c400;
    --flame-light: #f6e21a;
    --rule: #333;
  }
  * { box-sizing: border-box; margin: 0; padding: 0; }
  html, body { width: 1200px; height: 801px; overflow: hidden; }
  body {
    background: var(--page);
    display: flex; align-items: center; justify-content: center; gap: 40px;
    font-family: "Montserrat", Arial, sans-serif;
  }
  .card {
    position: relative; width: 540px; height: 309px; overflow: hidden;
    box-shadow: 0 10px 26px rgba(0,0,0,.18);
  }

  /* Front */
  .card--front { background: var(--card-white); }
  .edge-band {
    position: absolute; top: 0; right: 0; width: 14px; height: 100%;
    background: linear-gradient(to bottom, var(--plum) 0 45%, var(--flame-orange) 45% 80%, var(--flame-yellow) 80%);
  }
  .brand {
    position: absolute; left: 34px; top: 0; height: 100%;
    display: flex; align-items: center; gap: 12px;
  }
  .brand__dot { width: 44px; height: 44px; border-radius: 50%; background: var(--plum); flex: none; }
  .brand__name {
    font-weight: 700; font-size: 21px;
    letter-spacing: 1.5px; color: var(--ink); text-transform: uppercase; line-height: 1.15;
  }
  .divider {
    position: absolute; left: 262px; top: 64px; width: 1px; height: 182px; background: var(--rule);
  }
  .website {
    position: absolute; left: 284px; top: 0; height: 100%;
    display: flex; align-items: center; gap: 8px;
    font-weight: 500; font-size: 14px; color: var(--ink-soft);
  }
  .website__icon { width: 13px; height: 13px; flex: none; }

  /* Back */
  .card--back {
    background: linear-gradient(100deg, var(--flame-yellow) 0%, #f6b800 40%, var(--flame-orange) 78%, var(--flame-deep) 100%);
  }
  .flame-art {
    position: absolute; left: 0; top: 40px; width: 320px; height: 269px;
    background: radial-gradient(closest-side at 50% 70%, var(--flame-light) 0%, rgba(246,200,0,.6) 50%, rgba(246,180,0,0) 100%);
  }
  .back-brand {
    position: absolute; right: 34px; bottom: 80px; text-align: right;
    font-weight: 700; font-size: 26px;
    letter-spacing: 2px; color: #fff; text-transform: uppercase;
  }
  .back-brand__rule { display: block; width: 200px; height: 1px; background: #fff; margin: 8px 0 0 auto; }
</style>
</head>
<body>
  <section class="card card--front" aria-label="Business card front">
    <div class="brand">
      <span class="brand__dot"></span>
      <span class="brand__name">Ferncrest<br>Roam</span>
    </div>
    <div class="divider"></div>
    <p class="website">
      <svg class="website__icon" viewBox="0 0 12 12"><circle cx="6" cy="6" r="5.5" fill="var(--accent-red)"/><circle cx="6" cy="6" r="2" fill="none" stroke="#fff" stroke-width="1"/></svg>
      www.ferncrestroam.example
    </p>
    <div class="edge-band"></div>
  </section>

  <section class="card card--back" aria-label="Business card back">
    <div class="flame-art" role="img" aria-label="Large stylised flame illustration in yellow and orange"></div>
    <div class="back-brand">
      Ferncrest Roam
      <span class="back-brand__rule"></span>
    </div>
  </section>
</body>
</html>
```